Modern Business Card

Modern professional business card with more than just logo and demographic info. Something memorable.

We are a trendy/modern chiropractic group with an emphasis on neurology, hence the minimalist-type brain logo. We want to convey that modern and technical aspect with professionalism and the elite nature of our practice environment.

```html
<!DOCTYPE html>
<html lang="en">
<head>
<meta charset="utf-8">
<title>Vantage Chiropractic – Business Card</title>
<link rel="stylesheet" href="https://fonts.googleapis.com/css2?family=Lora:wght@400;500&family=Khand:wght@500&display=swap">
<style>
  :root {
    --page-bg: #b9b9b9;
    --brand-blue: #3d62a1;
    --brand-blue-deep: #3a5c98;
    --card-white: #f2f2f4;
    --card-white-shade: #e4e5e8;
    --ink-dark: #241f25;
    --ink-body: #3a3a40;
    --band-dark: #3a3238;
    --front-text: #e9eaee;
    --band-text: #e6e6ea;
  }
  * { margin: 0; padding: 0; box-sizing: border-box; }
  html, body { width: 1200px; height: 576px; overflow: hidden; }
  body {
    background: var(--page-bg);
    font-family: "Lora", serif;
    position: relative;
  }
  .card {
    position: absolute;
    width: 484px;
    height: 292px;
    border-radius: 10px;
    overflow: hidden;
  }
  /* Front side */
  .card-front {
    left: 82px;
    top: 139px;
    background: linear-gradient(180deg, var(--brand-blue) 0%, var(--brand-blue-deep) 100%);
  }
  .front-wordmark {
    position: absolute;
    left: 0;
    right: 0;
    top: 112px;
    text-align: center;
    color: var(--front-text);
    font-weight: 400;
    line-height: 1;
  }
  .front-wordmark .line-main { display: block; font-size: 60px; letter-spacing: 1px; }
  .front-wordmark .line-sub { display: block; font-size: 37px; margin-top: 2px; letter-spacing: 0.5px; }

  /* Back side */
  .card-back {
    left: 602px;
    top: 138px;
    background: linear-gradient(180deg, var(--card-white) 0%, var(--card-white-shade) 100%);
  }
  .brand-lockup {
    position: absolute;
    left: 34px;
    top: 106px;
    display: flex;
    align-items: center;
    gap: 12px;
  }
  .brand-square {
    width: 40px;
    height: 40px;
    background: var(--brand-blue);
  }
  .brand-name {
    color: var(--ink-dark);
    font-weight: 400;
    line-height: 1;
  }
  .brand-name .line-main { display: block; font-size: 34px; letter-spacing: 0.5px; }
  .brand-name .line-sub { display: block; font-size: 21px; margin-top: 1px; letter-spacing: 0.3px; }

  .contact-block {
    position: absolute;
    left: 275px;
    top: 84px;
  }
  .person-name {
    font-family: "Khand", sans-serif;
    font-weight: 500;
    font-size: 22px;
    color: var(--brand-blue);
    line-height: 1.1;
  }
  .person-title {
    font-size: 12px;
    color: var(--ink-body);
    margin-top: 3px;
  }
  .contact-list {
    list-style: none;
    margin-top: 14px;
  }
  .contact-list li {
    display: flex;
    align-items: center;
    gap: 10px;
    font-size: 12px;
    color: var(--ink-body);
    height: 18.5px;
  }
  .contact-list svg { width: 11px; height: 11px; flex: none; }

  .address-band {
    position: absolute;
    left: 0;
    right: 0;
    bottom: 0;
    height: 36px;
    background: linear-gradient(90deg, var(--band-dark) 0%, var(--band-dark) 8%, var(--brand-blue) 100%);
    color: var(--band-text);
    font-size: 12px;
    display: flex;
    align-items: center;
    justify-content: center;
    letter-spacing: 0.2px;
  }
</style>
</head>
<body>

<section class="card card-front" aria-label="Business card front">
  <h1 class="front-wordmark">
    <span class="line-main">VANTAGE</span>
    <span class="line-sub">CHIROPRACTIC</span>
  </h1>
</section>

<section class="card card-back" aria-label="Business card back">
  <div class="brand-lockup">
    <div class="brand-square"></div>
    <div class="brand-name">
      <span class="line-main">VANTAGE</span>
      <span class="line-sub">CHIROPRACTIC</span>
    </div>
  </div>

  <div class="contact-block">
    <p class="person-name">Alex Rowan Hale</p>
    <p class="person-title">Managing Director</p>
    <ul class="contact-list">
      <li>
        <svg viewBox="0 0 12 12" aria-hidden="true"><path fill="#3d62a1" d="M1 4.2C1 2.8 3 1.5 6 1.5s5 1.3 5 2.7v1H8.5V4H3.5v1.2H1zM3.2 6h5.6l1.4 4.5H1.8zM6 6.9a1.4 1.4 0 1 0 0 2.8 1.4 1.4 0 0 0 0-2.8z"/></svg>
        555-204-3170
      </li>
      <li>
        <svg viewBox="0 0 12 12" aria-hidden="true"><path fill="#3d62a1" d="M0.5 2.5h11v7h-11zM1.5 3.4v.3L6 6.7l4.5-3v-.3z"/></svg>
        alex@vantagechiro.com
      </li>
      <li>
        <svg viewBox="0 0 12 12" aria-hidden="true"><g fill="none" stroke="#3d62a1" stroke-width="1"><circle cx="6" cy="6" r="5"/><ellipse cx="6" cy="6" rx="2.2" ry="5"/><path d="M1 6h10M2 3.3h8M2 8.7h8"/></g></svg>
        www.vantagechiro.com
      </li>
    </ul>
  </div>

  <div class="address-band">48 Meridian Ave., Lakeside, Fairview, US 204518</div>
</section>

</body>
</html>
```